Web Design Project

Bolt-Turn Dakota locksmiths are experts in the residential and
commercial Locksmith industry with over 20 year’s experience.
Our mission is to provide you the best service at the lowest price.
We accomplish our mission with our competitive up-front pricing, we are fast and reliable, providing superior customer service and backing up our work. Your satisfaction is always our top priority.
You can learn a lot about our companies at www.swiftlatchco.example and www.boltturndakota.example.  Other great site for you to look at is www.tumblr-pin.example, this is a site that we would like to be like.
We want a bold, clean site that gets our point across about the ease of re-keying your house and the security that comes with the knowledge that you are the only one that has keys to it.
All content can be taken from the www.boltturndakota.example.

Target Market(s)
Home Owners - Commercial Building Owners Age: 28-70 both men and women
Industry/Entity Type
Residential
Requirements
Must have
- We want to use the colors of orange, black and grey.  You will find our logo on both of the sites.  The main site to focus on is www.boltturndakota.example, this is the site where we will use the design you create.
Please leave a space on the home page for a ClipStream video in the center of the page. Include a place for Friendbook, Chirpnet, JobLoop and Rateit links.
We also would like a strong call to action to call us or go to the ordering page for service.
Must have the home page, contact us page and an typical design template for the other pages.

```html
<!DOCTYPE html>
<html lang="en">
<head>
<meta charset="utf-8">
<title>Bolt-Turn Dakota — About Us</title>
<link rel="stylesheet" href="https://fonts.googleapis.com/css2?family=Source+Sans+3:wght@400;600&family=Arimo:wght@400&display=swap">
<style>
  :root {
    --page-bg: #1b1b1b;
    --page-bg-light: #2a2a2a;
    --panel: #ffffff;
    --orange: #f7861c;
    --orange-dark: #e4700a;
    --ink: #222222;
    --ink-soft: #333333;
    --slider-dark: #232323;
    --footer-text: #a8a8a8;
  }
  * { box-sizing: border-box; margin: 0; padding: 0; }
  html, body { width: 1026px; height: 1200px; overflow: hidden; }
  body {
    position: relative;
    background: radial-gradient(ellipse at 50% 40%, var(--page-bg-light), var(--page-bg) 75%);
    font-family: "Arimo", Arial, sans-serif;
    color: var(--ink);
  }
  .page-panel {
    position: absolute; left: 53px; top: 42px; width: 927px; height: 1083px;
    background: var(--panel); border-radius: 5px;
    box-shadow: 0 0 10px rgba(0,0,0,.6);
    overflow: hidden;
  }
  .header-photo {
    position: absolute; left: 0; top: 0; width: 927px; height: 150px;
    background: linear-gradient(180deg, #c9cdd2 0%, #e6e8eb 45%, #f4f4f4 100%);
    opacity: .85;
  }
  .brand {
    position: absolute; left: 22px; top: 70px;
    display: flex; align-items: center; gap: 8px;
    font-family: "Source Sans 3", sans-serif; font-weight: 600;
    font-size: 24px; color: var(--ink);
  }
  .brand-square { width: 26px; height: 26px; background: var(--orange); }
  .site-title {
    position: absolute; left: 195px; top: 18px; width: 300px; text-align: center;
    font-family: "Source Sans 3", sans-serif; font-weight: 400; color: var(--ink);
  }
  .site-title h1 { font-size: 35px; font-weight: 400; line-height: 42px; }
  .site-title .by-line { font-size: 17px; margin-top: 10px; }
  .site-title .tagline { font-size: 17px; margin-top: 12px; }
  .call-box {
    position: absolute; right: 30px; top: 44px; width: 160px; text-align: center;
    font-family: "Source Sans 3", sans-serif;
  }
  .call-box .label { font-size: 18px; color: var(--ink); }
  .call-box .phone { font-size: 25px; color: var(--orange); margin-top: 6px; }

  .main-nav {
    position: absolute; left: 5px; top: 146px; width: 917px; height: 40px;
    background: linear-gradient(180deg, #fb9a35 0%, var(--orange) 50%, var(--orange-dark) 100%);
    border-radius: 4px;
  }
  .main-nav a {
    position: absolute; top: 13px; font-size: 13px; color: #111; text-decoration: none;
  }
  .main-nav a.current {
    top: 3px; height: 32px; line-height: 32px; padding: 0 17px;
    background: linear-gradient(180deg, #ffffff, #dcdcdc);
    border-radius: 4px; box-shadow: 0 2px 3px rgba(0,0,0,.35);
  }

  .slider { position: absolute; left: 7px; top: 197px; width: 913px; height: 410px; }
  .slider svg { position: absolute; left: 0; top: 0; }
  .slide-photo {
    position: absolute; left: 17px; top: 12px; width: 881px; height: 327px;
    background: linear-gradient(90deg, #b9801f 0%, #d49a3a 30%, #9b5226 60%, #5a2c17 85%, #3c1e12 100%);
  }
  .slide-caption {
    position: absolute; left: 17px; top: 110px; width: 288px; height: 128px;
    background: rgba(40,30,20,.82); padding: 18px 12px;
    font-family: "Source Sans 3", sans-serif; color: #fff;
  }
  .slide-caption .special { font-size: 20px; line-height: 22px; }
  .slide-caption .price { font-size: 33px; line-height: 34px; color: var(--orange); }
  .slide-caption .sub { font-size: 20px; line-height: 30px; margin-top: 2px; }
  .slider-dots { position: absolute; top: 352px; left: 421px; display: flex; gap: 13px; }
  .slider-dots span {
    width: 18px; height: 18px; border-radius: 50%;
    background: radial-gradient(circle at 40% 35%, #ffb45a, var(--orange-dark));
  }
  .slider-dots span.active { background: radial-gradient(circle at 40% 35%, #ffffff, #bbbbbb); }

  .about { position: absolute; left: 47px; top: 620px; width: 548px; }
  .about h2 {
    font-family: "Source Sans 3", sans-serif; font-weight: 400; font-size: 23px;
    color: var(--ink); padding-left: 5px; width: 307px; padding-bottom: 4px;
    border-bottom: 1px dotted #555;
  }
  .about p { font-size: 11.5px; line-height: 24.6px; color: var(--ink-soft); padding-left: 4px; }
  .about .intro { margin-top: 16px; }
  .about h3 { font-size: 14px; font-weight: 400; margin-top: 45px; padding-left: 5px; color: var(--ink); }
  .about .second { margin-top: 33px; width: 545px; }

  .side-photo {
    position: absolute; left: 655px; top: 682px; width: 228px; height: 205px;
    border: 1px solid #ddd; padding: 3px; background: #fff;
    box-shadow: 0 0 3px rgba(0,0,0,.12);
  }
  .side-photo div {
    width: 100%; height: 100%;
    background: linear-gradient(135deg, #e4e3ec 0%, #c9c7d2 60%, #b7a66a 100%);
  }

  .social { position: absolute; left: 64px; top: 1151px; display: flex; gap: 3px; }
  .social a { width: 23px; height: 22px; border-radius: 3px; background: #3d8fd1; display: block; }
  .footer-links {
    position: absolute; right: 50px; top: 1139px; font-size: 11px; color: var(--footer-text);
    word-spacing: 1px;
  }
  .copyright { position: absolute; right: 47px; top: 1163px; font-size: 11px; color: var(--footer-text); }
</style>
</head>
<body>
  <div class="page-panel">
    <div class="header-photo" role="img" aria-label="Faded photo of a white suburban house"></div>
    <div class="brand"><span class="brand-square"></span>Swift-Latch</div>
    <div class="site-title">
      <h1>Bolt-Turn Dakota</h1>
      <div class="by-line">by Swift-Latch</div>
      <div class="tagline">"The smarter way to Security"</div>
    </div>
    <div class="call-box">
      <div class="label">Call us now</div>
      <div class="phone">555-014-2250</div>
    </div>

    <nav class="main-nav">
      <a style="left:32px">Home</a>
      <a class="current" style="left:89px">About Us</a>
      <a style="left:195px">Rekey Special</a>
      <a style="left:313px">Services</a>
      <a style="left:399px">Property Manager</a>
      <a style="left:538px">Commercial Property</a>
      <a style="left:697px">Order Services</a>
      <a style="left:819px">Contact Us</a>
    </nav>

    <div class="slider">
      <svg width="913" height="410" viewBox="0 0 913 410" aria-hidden="true">
        <defs>
          <filter id="curve-shadow" x="-5%" y="-5%" width="110%" height="120%">
            <feGaussianBlur stdDeviation="5"/>
          </filter>
        </defs>
        <path d="M0 0 H913 V345 C780 330 640 340 540 372 C470 395 400 398 330 378 C220 345 100 338 0 350 Z" fill="#000" opacity=".35" filter="url(#curve-shadow)" transform="translate(0,5)"/>
        <path d="M0 0 H913 V345 C780 330 640 340 540 372 C470 395 400 398 330 378 C220 345 100 338 0 350 Z" fill="var(--slider-dark)"/>
      </svg>
      <div class="slide-photo" role="img" aria-label="Brass door lock and handle on a wooden door in warm light"></div>
      <div class="slide-caption">
        <div class="special">The Dakota Rekey Special</div>
        <div class="price">$89.95</div>
        <div class="sub">Rekey Any Home</div>
      </div>
      <div class="slider-dots"><span class="active"></span><span></span><span></span></div>
    </div>

    <section class="about">
      <h2>About Us</h2>
      <p class="intro">Lorem Ipsum is simply dummy text of the printing and typesetting industry. Lorem Ipsum has been the industry's standard dummy text ever since the 1500s, when an unknown printer took a galley of type and scrambled it to make a type specimen book. It has survived not only five centuries, but also the leap into electronic typesetting, remaining essentially unchanged. It was popularised in the 1960s with the release of Inkrub sheets containing Lorem Ipsum passages, and more recently with desktop publishing software like Pagewright Studio including versions of Lorem Ipsum</p>
      <h3>Sub Heading</h3>
      <p class="second">Lorem Ipsum passage, and going through the cites of the word in classical literature, discovered the undoubtable source. Lorem Ipsum comes from sections 1.10.32 and 1.10.33 of "de Rebus Minoribus et Maioribus" Arvelius, written in 45 BC. This book is a treatise on the theory of ethics, very popular during the Renaissance. The first line of Lorem Ipsum, "Lorem ipsum dolor sit amet..", comes from a line in section.</p>
    </section>

    <div class="side-photo"><div role="img" aria-label="Brass lock cylinder with a key inserted, on a pale background"></div></div>
  </div>

  <div class="social">
    <a aria-label="Chirpnet"></a><a aria-label="JobLoop"></a><a aria-label="Friendbook"></a><a aria-label="Plusring"></a>
  </div>
  <div class="footer-links">Privacy &amp; Legal &nbsp;|&nbsp; Site Map &nbsp;|&nbsp; Contact Us</div>
  <div class="copyright">© 2012 Bolt-Turn Dakota. All rights reserved</div>
</body>
</html>
```